Business Card Design Project

- makeup artist business card

- original and creative

- Elegant design

- Feel free to come out with cool designs but stick to being elegant and attractive

- Design relates to makeup

- includes name, occupation, contact numbers, email, website

- regular size business card

- round corner card

- double sided

- on 1 side it should just have the website name in the center " moonveilstudio.net "

Industry/Entity Type

Business

Requirements
Must have
• Delia Marsh
Makeup Artist
USA: +1 (415)772-0461
Singapore: +65 82307915
deliamarsh@moonveilstudio.net
www.moonveilstudio.net
Should not have
• nothing cartoon looking.
Pictures of makeup being grab from the internet.. Examples: eyes or lips.

```html
<!DOCTYPE html>
<html lang="en">
<head>
<meta charset="utf-8">
<title>Delia Marsh – Makeup Artist Business Card</title>
<link href="https://fonts.googleapis.com/css2?family=Open+Sans:wght@400;600&family=PT+Serif:ital,wght@0,700;1,400&display=swap" rel="stylesheet">
<style>
  :root {
    --page-bg: #f3eef0;
    --plum-deep: #7a2160;
    --plum-mid: #962a6c;
    --plum-glow: #a9346f;
    --plum-ghost: #b95793;
    --rose-card: #c8578f;
    --rose-light: #d46ea0;
    --stripe-dark: #8b2a66;
    --artist-tone: #7b2c63;
    --white: #ffffff;
  }
  * { margin: 0; padding: 0; box-sizing: border-box; }
  html, body {
    width: 1200px;
    height: 951px;
    overflow: hidden;
    background: var(--page-bg);
    font-family: "Open Sans", Verdana, sans-serif;
  }
  .canvas {
    position: relative;
    width: 1200px;
    height: 951px;
  }
  .card {
    position: absolute;
    width: 640px;
    height: 366px;
    border-radius: 30px;
    overflow: hidden;
    box-shadow: 0 6px 18px rgba(80, 20, 60, 0.22);
  }

  /* Front side */
  .card-front {
    left: 80px;
    top: 60px;
    background: radial-gradient(ellipse at 45% 40%, var(--plum-glow) 0%, var(--plum-mid) 45%, var(--plum-deep) 100%);
  }
  .brand-ghost {
    position: absolute;
    left: 30px;
    top: 14px;
    color: var(--plum-ghost);
    font-family: "Open Sans", Verdana, sans-serif;
    font-weight: 400;
    font-size: 60px;
    line-height: 64px;
    letter-spacing: 1px;
  }
  .brand-ghost span { display: block; }
  .brand-ghost .word-2 { padding-left: 60px; }
  .brand-ghost .word-3 { padding-left: 66px; }
  .front-url {
    position: absolute;
    left: 120px;
    top: 222px;
    color: var(--white);
    font-size: 28px;
    letter-spacing: 0.5px;
  }

  /* Back side */
  .card-back {
    left: 480px;
    top: 500px;
    background: var(--rose-card);
  }
  .side-stripe {
    position: absolute;
    top: 0;
    left: 50px;
    height: 100%;
    display: flex;
  }
  .side-stripe .band-light { width: 18px; background: var(--rose-light); }
  .side-stripe .rule { width: 4px; background: var(--white); }
  .side-stripe .band-dark { width: 34px; background: var(--stripe-dark); margin: 0 4px; }
  .identity {
    position: absolute;
    right: 42px;
    top: 72px;
    text-align: right;
  }
  .identity .name {
    font-family: "PT Serif", Georgia, serif;
    font-weight: 700;
    font-size: 25px;
    color: var(--white);
  }
  .identity .role {
    font-family: "PT Serif", Georgia, serif;
    font-style: italic;
    font-size: 18px;
    color: var(--artist-tone);
    margin-top: -2px;
  }
  .contact-list {
    position: absolute;
    left: 150px;
    top: 218px;
    list-style: none;
    color: var(--white);
    font-size: 17px;
    line-height: 26px;
  }
  .contact-list li { display: flex; align-items: center; }
  .contact-list svg { width: 16px; height: 16px; margin-right: 10px; flex-shrink: 0; }
</style>
</head>
<body>
<main class="canvas">

  <section class="card card-front" aria-label="Card front">
    <div class="brand-ghost" aria-hidden="true">
      <span class="word-1">moon</span>
      <span class="word-2">veil</span>
      <span class="word-3">studio</span>
    </div>
    <p class="front-url">www.moonveilstudio.net</p>
  </section>

  <section class="card card-back" aria-label="Card back">
    <div class="side-stripe" aria-hidden="true">
      <div class="band-light"></div>
      <div class="rule"></div>
      <div class="band-dark"></div>
      <div class="rule"></div>
    </div>

    <div class="identity">
      <p class="name">Delia Marsh</p>
      <p class="role">Makeup Artist</p>
    </div>

    <ul class="contact-list">
      <li>
        <svg viewBox="0 0 16 16" aria-hidden="true"><path d="M5 2 C2 3 1.5 6 3 9 C5 13 9 15 12 14 L13.5 11.5 L10.5 9.5 L9 11 C7 10 6 9 5 7 L6.5 5.5 L5 2 Z" fill="#fff"/></svg>
        USA: +1 (415)772-0461
      </li>
      <li>
        <svg viewBox="0 0 16 16" aria-hidden="true"><path d="M5 2 C2 3 1.5 6 3 9 C5 13 9 15 12 14 L13.5 11.5 L10.5 9.5 L9 11 C7 10 6 9 5 7 L6.5 5.5 L5 2 Z" fill="#fff"/></svg>
        Singapore: +65 82307915
      </li>
      <li>
        <svg viewBox="0 0 16 16" aria-hidden="true"><rect x="1.5" y="4" width="13" height="9" rx="1" fill="#fff"/><path d="M1.5 4.5 L8 9.5 L14.5 4.5" fill="none" stroke="#c8578f" stroke-width="1.3"/></svg>
        deliamarsh@moonveilstudio.net
      </li>
      <li>
        <svg viewBox="0 0 16 16" aria-hidden="true"><circle cx="8" cy="8" r="6.5" fill="#fff"/></svg>
        www.moonveilstudio.net
      </li>
    </ul>
  </section>

</main>
</body>
</html>
```